Business Card for Coastal Tundrabridge Advisory

We need a business card for Coastal Tundrabridge Advisory. The company website address is provided below. The company logo is attached. We provide specialized permafrost services to the mining, transportation, and oil & gas industries. The card should be prepared for:
Matthias Korhonen, PhD.
Coastal Tundrabridge Advisory
PO Box 418259
Quillwater, Alaska 99642
Direct: +1-907-555-0143
Email: mkorhonen@tundrabridgeadvisory.example
Website: www.coastaltundrabridgeadvisory.example

```html
<!DOCTYPE html>
<html lang="en">
<head>
<meta charset="utf-8">
<title>Coastal Tundrabridge Advisory — Business Card</title>
<link href="https://fonts.googleapis.com/css2?family=Quicksand:wght@400;500;700&display=swap" rel="stylesheet">
<style>
  :root {
    --backdrop: #acacac;
    --card-front: #464646;
    --card-back: #ffffff;
    --mark-dark: #1c2530;
    --mark-light: #a3a3a3;
    --ink: #3a3a3a;
    --ink-soft: #4a4a4a;
    --rule: #9a9a9a;
  }
  * { box-sizing: border-box; margin: 0; padding: 0; }
  html, body { width: 1200px; height: 1000px; overflow: hidden; }
  body {
    background: var(--backdrop);
    font-family: "Quicksand", sans-serif;
    position: relative;
  }
  .card {
    position: absolute;
    left: 293px;
    width: 615px;
    height: 354px;
    border-radius: 16px;
    box-shadow: 0 3px 8px rgba(0,0,0,0.25);
  }
  .card--front { top: 132px; background: var(--card-front); }
  .card--back { top: 530px; background: var(--card-back); }

  .wordmark {
    position: absolute;
    font-weight: 700;
    text-transform: uppercase;
    white-space: nowrap;
  }
  .card--front .wordmark {
    left: 0; right: 0; top: 162px;
    text-align: center;
    font-size: 21px;
    letter-spacing: 2px;
    color: var(--mark-dark);
  }
  .card--back .wordmark {
    right: 29px; top: 54px;
    font-size: 14px;
    letter-spacing: 1.4px;
    color: var(--mark-light);
  }

  .holder { position: absolute; left: 26px; top: 190px; color: var(--ink); }
  .holder__name { font-weight: 700; font-size: 14px; letter-spacing: 0.3px; line-height: 17px; }
  .holder__company { font-size: 13.5px; line-height: 17px; color: var(--ink-soft); }
  .address { position: absolute; left: 25px; top: 236px; font-size: 13.5px; line-height: 17px; color: var(--ink-soft); }

  .rule { position: absolute; left: 29px; right: 29px; top: 286px; border-top: 1px solid var(--rule); }

  .contacts { position: absolute; left: 32px; top: 299px; list-style: none; font-size: 13px; line-height: 17px; color: var(--ink-soft); }
  .contacts li { display: flex; align-items: center; gap: 6px; }
  .contacts svg { width: 12px; height: 12px; fill: var(--ink); }

  .website { position: absolute; right: 29px; top: 316px; font-size: 13px; line-height: 17px; color: var(--ink); }
  .website strong { font-weight: 700; }
</style>
</head>
<body>
  <section class="card card--front" aria-label="Card front">
    <div class="wordmark">Coastal Tundrabridge Advisory</div>
  </section>

  <section class="card card--back" aria-label="Card back">
    <div class="wordmark">Coastal Tundrabridge Advisory</div>

    <div class="holder">
      <p class="holder__name">MATTHIAS KORHONEN, PHD.</p>
      <p class="holder__company">Coastal Tundrabridge Advisory</p>
    </div>

    <address class="address" style="font-style:normal">
      PO Box 418259<br>
      Quillwater, Alaska 99642
    </address>

    <div class="rule"></div>

    <ul class="contacts">
      <li>
        <svg viewBox="0 0 24 24" aria-hidden="true"><path d="M6.6 10.8a15.1 15.1 0 0 0 6.6 6.6l2.2-2.2c.3-.3.7-.4 1-.2 1.1.4 2.3.6 3.6.6.6 0 1 .4 1 1V20c0 .6-.4 1-1 1C10.6 21 3 13.4 3 4c0-.6.4-1 1-1h3.5c.6 0 1 .4 1 1 0 1.3.2 2.5.6 3.6.1.3 0 .7-.2 1z"/></svg>
        (907) 555-0143
      </li>
      <li>
        <svg viewBox="0 0 24 24" aria-hidden="true"><path d="M2 5h20v14H2z M3.5 6.5 12 12.5l8.5-6" /><path d="M2 5l10 7 10-7v2l-10 7L2 7z" fill="#fff"/></svg>
        mkorhonen@tundrabridgeadvisory.example
      </li>
    </ul>

    <p class="website"><strong>coastaltundrabridgeadvisory</strong>.example</p>
  </section>
</body>
</html>
```